New layout on letterheads, businesscards, flyers, brochures etc.

Dear Sir,
We would like to change our layout a bit. We would like to have the same look on everything we make and still keep our logo. We would like some suggestions suitable for a company like ours, where solar systems, heat pumps and LED lighting is reflected. We like our blue colour in our logo (#009ddf) and some of the black reflected in our solar panels and we like the solar cell (almost square with soft corners). We like soft lines, clean look and reflecting expensive solar panels from the very best distributors (QX, Halvorenti, Kestrel Arcwave etc.). We want a light, soft, exclusive and expensive look to it all. We need this for business cards, letterhead/bottom, flyers, brochures and stickers etc.
Thank you in advance.

Tavurn
Lindvej 28 B
8215 Vesterby
Denmark

info@tavurn.dk
www.tavurn.dk

```html
<!DOCTYPE html>
<html lang="da">
<head>
<meta charset="utf-8">
<title>Tavurn – stationery set</title>
<link rel="stylesheet" href="https://fonts.googleapis.com/css2?family=Open+Sans:ital,wght@0,400;0,600;0,700;1,600&display=swap">
<style>
  :root {
    --brand-blue: #009ddf;
    --brand-blue-deep: #1a8fcc;
    --panel-black: #17191c;
    --ink: #3b3f44;
    --ink-soft: #7a8088;
    --paper: #ffffff;
    --board: #eceff2;
    --sky-top: #cfe0ee;
    --sky-low: #f1f5f8;
    --grass: #6aa83a;
    --grass-deep: #4f8d2a;
    --mesh-tint: #f2f4f6;
  }
  * { box-sizing: border-box; margin: 0; padding: 0; }
  html, body { width: 1200px; height: 848px; overflow: hidden; }
  body { background: var(--board); font-family: "Open Sans", Arial, sans-serif; color: var(--ink); }

  .board { position: relative; width: 1200px; height: 848px; overflow: hidden; }
  .sheet { position: absolute; background: var(--paper); overflow: hidden; box-shadow: 0 2px 10px rgba(0,0,0,.08); }

  /* brand name block */
  .brand { display: flex; align-items: center; gap: 6px; }
  .brand-square { background: var(--brand-blue); border-radius: 3px; flex: none; }
  .brand-name { font-weight: 700; color: var(--ink-soft); letter-spacing: .02em; line-height: 1; }

  /* letterhead */
  .letterhead { left: 40px; top: 40px; width: 356px; height: 503px; }
  .letterhead .brand { position: absolute; left: 30px; top: 30px; }
  .letterhead .brand-square { width: 15px; height: 15px; }
  .letterhead .brand-name { font-size: 15px; }
  .letterhead-address { position: absolute; left: 30px; top: 398px; font-size: 7.5px; line-height: 1.5; color: var(--ink-soft); font-style: normal; }
  .letterhead-address .gap { margin-top: 6px; }
  .letterhead-address .web { color: var(--brand-blue); font-weight: 600; margin-top: 4px; }
  .swoosh { position: absolute; left: 0; bottom: 0; width: 100%; }

  /* business card */
  .card-front { left: 40px; top: 573px; width: 356px; height: 230px; }
  .card-front .brand { position: absolute; left: 24px; top: 24px; }
  .card-front .brand-square { width: 14px; height: 14px; }
  .card-front .brand-name { font-size: 14px; }
  .card-web { position: absolute; right: 24px; top: 27px; font-size: 8.5px; font-weight: 600; color: var(--brand-blue); }
  .card-person { position: absolute; left: 150px; top: 88px; }
  .card-name { font-size: 12.5px; font-weight: 600; color: var(--brand-blue); }
  .card-role { font-size: 8.5px; color: var(--ink-soft); margin-bottom: 10px; }
  .card-line { font-size: 8.5px; line-height: 1.55; color: var(--ink); }

  .card-back { left: 426px; top: 573px; width: 356px; height: 230px;
    background: radial-gradient(ellipse at 50% 40%, #25282c 0%, var(--panel-black) 70%); }
  .card-back .brand { position: absolute; left: 50%; top: 50%; transform: translate(-50%, -50%); gap: 12px; }
  .card-back .brand-square { width: 34px; height: 34px; border-radius: 6px; }
  .card-back .brand-name { font-size: 38px; color: #e6e8ea; }

  /* flyer */
  .flyer { left: 426px; top: 40px; width: 356px; height: 503px; }
  .flyer-photo { position: absolute; left: 0; top: 0; width: 100%; height: 338px;
    background: linear-gradient(180deg, var(--sky-top) 0%, var(--sky-low) 52%, var(--grass) 60%, var(--grass-deep) 100%); }
  .flyer .brand { position: absolute; left: 20px; top: 22px; }
  .flyer .brand-square { width: 18px; height: 18px; }
  .flyer .brand-name { font-size: 18px; }
  .partner-name { position: absolute; font-weight: 700; color: var(--ink); }
  .flyer .partner-name { right: 20px; top: 22px; font-size: 16px; }
  .flyer-contact { position: absolute; left: 20px; top: 62px; }
  .flyer-contact h2 { font-size: 13px; font-weight: 600; color: var(--ink); margin-bottom: 6px; }
  .flyer-contact p { font-size: 7px; line-height: 1.5; font-weight: 600; color: var(--ink); }
  .flyer-wave { position: absolute; left: 0; top: 296px; width: 100%; }
  .flyer-mesh { position: absolute; left: 0; top: 352px; width: 100%; height: 151px;
    background: linear-gradient(160deg, var(--paper) 0%, var(--mesh-tint) 100%); }
  .flyer-copy { position: absolute; left: 20px; right: 20px; top: 364px; }
  .flyer-copy h3 { font-size: 11px; font-style: italic; font-weight: 600; color: var(--brand-blue-deep); margin-bottom: 6px; }
  .flyer-copy p { font-size: 7.2px; line-height: 1.5; color: var(--ink); }

  /* brochure */
  .brochure { left: 812px; top: 301px; width: 348px; height: 246px; display: flex; }
  .fold { position: relative; width: 116px; height: 100%; overflow: hidden; }
  .fold + .fold { border-left: 1px solid rgba(0,0,0,.06); }
  .fold-questions { background: var(--brand-blue-deep); padding: 30px 12px 0; color: #fff; }
  .faq-item { margin-bottom: 16px; }
  .faq-q { font-size: 5.6px; font-weight: 700; line-height: 1.4; }
  .faq-a { font-size: 5.2px; line-height: 1.4; opacity: .9; }

  .fold-faq { background: var(--brand-blue-deep); color: #fff; }
  .faq-photo { position: absolute; left: 0; top: 0; width: 100%; height: 92px;
    background: linear-gradient(160deg, #e9eef2 0%, #c3ccd4 45%, #2b3a52 70%, #1e2a3e 100%); }
  .faq-head { position: absolute; left: 12px; right: 10px; top: 104px; }
  .faq-head h2 { font-size: 15px; font-weight: 700; line-height: 1; }
  .faq-head span { display: block; font-size: 4.6px; font-weight: 600; letter-spacing: .06em; margin-top: 2px; }
  .faq-head .faq-item { margin-top: 8px; }
  .faq-contact { position: absolute; left: 12px; bottom: 14px; font-size: 5px; line-height: 1.5; }
  .faq-contact strong { display: block; font-size: 6px; }

  .fold-cover { background: var(--paper); }
  .fold-cover .partner-name { right: 10px; top: 8px; font-size: 8px; }
  .cover-photo { position: absolute; left: 0; top: 22px; width: 100%; height: 96px;
    background: linear-gradient(180deg, var(--sky-top) 0%, var(--sky-low) 45%, var(--grass) 58%, var(--grass-deep) 100%); }
  .cover-wave { position: absolute; left: 0; top: 104px; width: 100%; }
  .cover-mesh { position: absolute; left: 0; top: 128px; width: 100%; height: 118px;
    background: linear-gradient(160deg, var(--paper) 0%, var(--mesh-tint) 100%); }
  .fold-cover .brand { position: absolute; left: 50%; top: 196px; transform: translateX(-50%); gap: 4px; }
  .fold-cover .brand-square { width: 10px; height: 10px; border-radius: 2px; }
  .fold-cover .brand-name { font-size: 11px; }
</style>
</head>
<body>
<main class="board">

  <!-- Letterhead -->
  <section class="sheet letterhead" aria-label="Letterhead">
    <div class="brand"><span class="brand-square"></span><span class="brand-name">Tavurn</span></div>
    <address class="letterhead-address">
      <div>Lindvej 28 B</div>
      <div>8215 Vesterby</div>
      <div>Denmark</div>
      <div class="gap">Phone : P +45 30 18 52 70</div>
      <div>Email : info@tavurn.dk</div>
      <div class="web">www.tavurn.dk</div>
    </address>
    <svg class="swoosh" viewBox="0 0 356 60" height="60" aria-hidden="true">
      <defs>
        <linearGradient id="lh-band" x1="0" x2="356" y1="0" y2="0" gradientUnits="userSpaceOnUse">
          <stop offset="0" stop-color="#009ddf"/>
          <stop offset=".86" stop-color="#009ddf"/>
          <stop offset=".86" stop-color="#17191c"/>
          <stop offset="1" stop-color="#17191c"/>
        </linearGradient>
      </defs>
      <path d="M0 54 C 120 52, 250 42, 356 20" fill="none" stroke="url(#lh-band)" stroke-width="5"/>
    </svg>
  </section>

  <!-- Business card, front -->
  <section class="sheet card-front" aria-label="Business card front">
    <div class="brand"><span class="brand-square"></span><span class="brand-name">Tavurn</span></div>
    <div class="card-web">www.tavurn.dk</div>
    <div class="card-person">
      <div class="card-name">Anders Holm Vestergaard</div>
      <div class="card-role">Technical Manager and Partner</div>
      <div class="card-line">P +45 30 18 52 70</div>
      <div class="card-line">M +45 41 96 07 34</div>
      <div class="card-line">avh@tavurn.dk</div>
    </div>
    <svg class="swoosh" viewBox="0 0 356 40" height="40" aria-hidden="true">
      <path d="M0 40 L0 34 C 130 34, 260 28, 356 10 L356 40 Z" fill="#009ddf"/>
    </svg>
  </section>

  <!-- Business card, back -->
  <section class="sheet card-back" aria-label="Business card back">
    <div class="brand"><span class="brand-square"></span><span class="brand-name">Tavurn</span></div>
  </section>

  <!-- Flyer -->
  <section class="sheet flyer" aria-label="Flyer">
    <div class="flyer-photo" role="img" aria-label="Photo: smiling family holding a solar panel on a green meadow, house with solar roof behind"></div>
    <div class="brand"><span class="brand-square"></span><span class="brand-name">Tavurn</span></div>
    <div class="partner-name">QX</div>
    <div class="flyer-contact">
      <h2>Kontakt</h2>
      <p>Lindvej 28 B, 8215 Vesterby,<br>Denmark.<br>mail : info@tavurn.dk<br>Phone: +45 30 18 52 70</p>
    </div>
    <svg class="flyer-wave" viewBox="0 0 356 60" height="60" aria-hidden="true">
      <path d="M0 30 C 110 14, 250 14, 356 26 L356 60 L0 60 Z" fill="#009ddf"/>
      <path d="M0 48 C 110 34, 250 34, 356 44 L356 60 L0 60 Z" fill="#ffffff"/>
    </svg>
    <div class="flyer-mesh" role="img" aria-label="Soft grey connected-dot network pattern"></div>
    <div class="flyer-copy">
      <h3>Er du vores nye samarbejdspartner?</h3>
      <p>QX vægter kvaliteten meget højt og gennemtester derfor panelerne helt til de allermindste detaljer. Som et godt eksempel på det kan nævnes at alle panelerne gennemlyses ved en EL-test (Elektroluminescens-test), hvilket svarer til en røntgen test hos mennesker. Derved findes selv mikroskopiske revner, der er usynlige for det menneskelige øje. Kun fejlfrie paneler får lov til at forlade fabrikken.</p>
    </div>
  </section>

  <!-- Tri-fold brochure, outside -->
  <section class="sheet brochure" aria-label="Tri-fold brochure">
    <div class="fold fold-questions">
      <div class="faq-item">
        <div class="faq-q">Hvor lang tid holder et solcelleanlæg?</div>
        <div class="faq-a">Typisk mere end 25 år med fuld ydelse.</div>
      </div>
      <div class="faq-item">
        <div class="faq-q">Kan jeg selv montere panelerne?</div>
        <div class="faq-a">Vi anbefaler altid en autoriseret installatør.</div>
      </div>
      <div class="faq-item">
        <div class="faq-q">Hvad koster en varmepumpe i drift?</div>
        <div class="faq-a">Det afhænger af husets størrelse og isolering.</div>
      </div>
    </div>

    <div class="fold fold-faq">
      <div class="faq-photo" role="img" aria-label="Photo: installers in work clothes mounting solar panels on a roof"></div>
      <div class="faq-head">
        <h2>FAQ</h2>
        <span>FREQUENTLY ASKED QUESTIONS</span>
        <div class="faq-item">
          <div class="faq-q">Hvordan vedligeholder jeg mine paneler?</div>
          <div class="faq-a">Et enkelt eftersyn om året er nok.</div>
        </div>
      </div>
      <div class="faq-contact">
        <strong>Kontakt</strong>
        Lindvej 28 B, 8215 Vesterby<br>
        Tlf. +45 30 18 52 70<br>
        www.tavurn.dk
      </div>
    </div>

    <div class="fold fold-cover">
      <div class="partner-name">QX</div>
      <div class="cover-photo" role="img" aria-label="Photo: family holding a solar panel on a meadow with a house behind"></div>
      <svg class="cover-wave" viewBox="0 0 116 30" height="30" aria-hidden="true">
        <path d="M0 14 C 40 4, 80 4, 116 10 L116 30 L0 30 Z" fill="#009ddf"/>
        <path d="M0 24 C 40 16, 80 16, 116 20 L116 30 L0 30 Z" fill="#ffffff"/>
      </svg>
      <div class="cover-mesh" role="img" aria-label="Soft grey connected-dot network pattern"></div>
      <div class="brand"><span class="brand-square"></span><span class="brand-name">Tavurn</span></div>
    </div>
  </section>

</main>
</body>
</html>
```